Veldmark Supplies Business Card

Professional business card that stand out to our potential customers. Front and back with clean modern design

Industry/Entity Type

Oil and gas

Contact Information for Business Card

Name, address, website , office phone and cell number

Requirements
Must have
• Editable files for each employee

```html
<!DOCTYPE html>
<html lang="en">
<head>
<meta charset="utf-8">
<title>Veldmark Supplies Business Card</title>
<link href="https://fonts.googleapis.com/css2?family=Montserrat:wght@500;600;700;800&display=swap" rel="stylesheet">
<style>
  :root {
    --sky: #05aed6;
    --sky-deep: #0796ba;
    --signal-red: #f40309;
    --paper: #ffffff;
    --backdrop: #e9ecef;
    --ink-light: #ffffff;
  }
  * { box-sizing: border-box; margin: 0; padding: 0; }
  html, body { width: 1200px; height: 878px; overflow: hidden; }
  body {
    background: var(--backdrop);
    font-family: "Montserrat", Arial, sans-serif;
    position: relative;
  }
  .card {
    position: absolute;
    top: 129px;
    width: 360px;
    height: 620px;
    border-radius: 34px;
    overflow: hidden;
    box-shadow: 0 6px 18px rgba(0,0,0,0.18);
  }

  /* Back side */
  .card-back { left: 180px; background: var(--sky); }
  .back-brand {
    position: absolute;
    left: 250px;
    top: 90px;
    width: 440px;
    transform-origin: 0 0;
    transform: rotate(90deg);
    display: flex;
    align-items: center;
    gap: 16px;
  }
  .back-brand .mark-square {
    width: 26px; height: 26px;
    background: var(--signal-red);
    flex: none;
  }
  .back-brand .brand-name {
    font-weight: 800;
    font-size: 30px;
    letter-spacing: 3px;
    color: var(--signal-red);
    white-space: nowrap;
  }

  /* Front side */
  .card-front { left: 660px; background: var(--sky); }
  .front-top {
    position: absolute; inset: 0;
    width: 100%; height: 100%;
  }
  .front-brand {
    position: absolute;
    top: 34px; left: 30px;
    display: flex; align-items: center; gap: 10px;
  }
  .front-brand .mark-square {
    width: 18px; height: 18px; background: var(--signal-red);
  }
  .front-brand .brand-name {
    font-weight: 800;
    font-size: 19px;
    letter-spacing: 2px;
    color: var(--signal-red);
  }
  .contact-block {
    position: absolute;
    left: 0; right: 0;
    top: 300px;
    text-align: center;
    color: var(--ink-light);
  }
  .person-name {
    font-weight: 800;
    font-size: 25px;
    letter-spacing: 1px;
  }
  .person-role {
    display: flex; align-items: center; justify-content: center; gap: 10px;
    font-weight: 500; font-size: 14px; margin-top: 2px;
  }
  .person-role::before, .person-role::after {
    content: ""; width: 80px; height: 1.5px; background: var(--ink-light);
  }
  .icon-row {
    display: flex; justify-content: center; gap: 16px;
    margin-top: 18px;
  }
  .icon-tile {
    width: 34px; height: 34px; background: var(--signal-red);
    display: flex; align-items: center; justify-content: center;
  }
  .contact-lines {
    margin-top: 16px;
    font-weight: 500; font-size: 15px; line-height: 1.45;
  }
  .divider {
    width: 250px; height: 1.5px; background: var(--ink-light);
    margin: 14px auto;
  }
  .address {
    font-weight: 500; font-size: 15px; line-height: 1.45;
  }
</style>
</head>
<body>

  <section class="card card-back" aria-label="Card back">
    <div class="back-brand">
      <span class="mark-square"></span>
      <span class="brand-name">VELDMARK SUPPLIES</span>
    </div>
  </section>

  <section class="card card-front" aria-label="Card front">
    <svg class="front-top" viewBox="0 0 360 620" preserveAspectRatio="none" aria-hidden="true">
      <polygon points="0,0 360,0 360,120 0,265" fill="var(--paper)"/>
    </svg>
    <div class="front-brand">
      <span class="mark-square"></span>
      <span class="brand-name">VELDMARK SUPPLIES</span>
    </div>

    <div class="contact-block">
      <div class="person-name">DAREN HOLLOWAY</div>
      <div class="person-role">President</div>

      <div class="icon-row">
        <span class="icon-tile" aria-label="Office phone">
          <svg width="20" height="20" viewBox="0 0 24 24"><path fill="#fff" d="M3 9c0-3 4-5 9-5s9 2 9 5v2h-5V9c-1-.6-2.5-1-4-1s-3 .4-4 1v2H3z"/><rect x="6" y="12" width="12" height="8" rx="1" fill="#fff"/></svg>
        </span>
        <span class="icon-tile" aria-label="Mobile phone">
          <svg width="20" height="20" viewBox="0 0 24 24"><rect x="7" y="2" width="10" height="20" rx="2" fill="none" stroke="#fff" stroke-width="2"/><circle cx="12" cy="18" r="1.2" fill="#fff"/></svg>
        </span>
        <span class="icon-tile" aria-label="Email">
          <svg width="22" height="22" viewBox="0 0 24 24"><rect x="2" y="5" width="20" height="14" fill="#fff"/><path d="M2 5l10 8 10-8" fill="none" stroke="var(--signal-red)" stroke-width="1.6"/></svg>
        </span>
        <span class="icon-tile" aria-label="Website">
          <svg width="22" height="22" viewBox="0 0 24 24"><circle cx="12" cy="12" r="9" fill="none" stroke="#fff" stroke-width="2"/><path d="M3 12h18M12 3c3 3 3 15 0 18M12 3c-3 3-3 15 0 18" fill="none" stroke="#fff" stroke-width="1.5"/></svg>
        </span>
      </div>

      <div class="contact-lines">
        <div>555-214-0387</div>
        <div>000-000-9999</div>
        <div>info@example-youremail.com</div>
        <div>www.example-yourwebsite.com</div>
      </div>
      <div class="divider"></div>
      <div class="address">
        <div>2240 Harlow Ave, Ste</div>
        <div>100, Dallas, TX 75204</div>
      </div>
    </div>
  </section>

</body>
</html>
```